Business Card Design needed for start up company Halvora

In need of a new business card designed for a start up company based in Sydney, Halvora is a new start up innovative Company, our mission it to make property accessible for everyday Australian and to become the leading Real Estate platform in Australia. We want it to be fresh and clean.

Industry/Entity Type

Financial

Contact Information for Business Card

Section for Name
Section for Title

HALVORA - The Strength of Pooling
Mobile:
Direct:

Font styles to use
Sans Serif

Colors
33a6d7
0692cd
0255a3
ffffff

Requirements
Must have
• Logo, all business card details

```html
<!DOCTYPE html>
<html lang="en">
<head>
<meta charset="utf-8">
<title>Halvora Business Card</title>
<link rel="stylesheet" href="https://fonts.googleapis.com/css2?family=Source+Sans+3:wght@400;600&display=swap">
<style>
  :root {
    --sky: #33a6d7;
    --blue: #0692cd;
    --navy: #0255a3;
    --navy-deep: #1b3c78;
    --white: #ffffff;
    --paper: #f4f5f6;
    --backdrop: #e6e8eb;
  }
  * { box-sizing: border-box; margin: 0; padding: 0; }
  html, body {
    width: 1200px; height: 960px; overflow: hidden;
    background: var(--backdrop);
    font-family: "Source Sans 3", sans-serif;
  }
  .sheet {
    width: 1200px; height: 960px;
    display: flex; flex-direction: column; align-items: center; justify-content: center;
    gap: 48px;
  }
  .card {
    position: relative;
    width: 700px; height: 400px;
    overflow: hidden;
    box-shadow: 0 6px 18px rgba(0,0,0,.18);
  }
  .company-name {
    font-weight: 600; line-height: 1; letter-spacing: .5px; white-space: nowrap;
  }
  /* Back side */
  .card-back {
    background: linear-gradient(135deg, var(--blue), #2a9ad3 60%, var(--sky));
    display: flex; flex-direction: column; align-items: center; justify-content: center;
  }
  .card-back .company-name { color: var(--white); font-size: 84px; margin-top: -20px; }
  .tagline {
    position: absolute; bottom: 58px; left: 0; right: 0;
    text-align: center; color: var(--white); font-size: 19px; font-weight: 400;
  }
  /* Front side */
  .card-front { background: var(--paper); }
  .front-brand {
    position: absolute; left: 0; top: 0; width: 318px; height: 400px;
    display: flex; align-items: center; justify-content: center;
  }
  .card-front .company-name { color: var(--navy); font-size: 58px; }
  .panel-shape { position: absolute; left: 0; top: 0; }
  .contact {
    position: absolute; left: 372px; top: 112px; width: 310px;
    color: var(--white);
  }
  .person-name { color: var(--sky); font-weight: 600; font-size: 22px; letter-spacing: .5px; line-height: 1.2; }
  .person-title { font-size: 19px; line-height: 1.2; margin-top: 4px; }
  .address { font-size: 18px; line-height: 1.25; margin-top: 32px; }
  .lines { list-style: none; margin-top: 4px; }
  .lines li { display: flex; align-items: center; gap: 10px; font-size: 18px; line-height: 1.35; }
  .lines svg { width: 13px; height: 13px; flex: none; fill: var(--white); }
</style>
</head>
<body>
<main class="sheet">
  <section class="card card-back" aria-label="Card back">
    <p class="company-name">Halvora</p>
    <p class="tagline">The Strength of Pooling</p>
  </section>

  <section class="card card-front" aria-label="Card front">
    <div class="front-brand">
      <p class="company-name">Halvora</p>
    </div>
    <svg class="panel-shape" width="700" height="400" viewBox="0 0 700 400">
      <defs>
        <linearGradient id="panelFill" x1="0" y1="0" x2="1" y2="1">
          <stop offset="0" stop-color="#0255a3"/>
          <stop offset="1" stop-color="#1b3c78"/>
        </linearGradient>
      </defs>
      <polygon points="330,0 700,0 700,400 330,400 330,136 318,124 330,112" fill="#33a6d7"/>
      <polygon points="336,0 700,0 700,400 336,400 336,136 324,124 336,112" fill="url(#panelFill)"/>
    </svg>
    <div class="contact">
      <p class="person-name">MAREN ELLORY</p>
      <p class="person-title">CEO/FOUNDER</p>
      <p class="address">412 Harbour Row<br>Sydney, NSW 2000</p>
      <ul class="lines">
        <li><svg viewBox="0 0 16 16"><path d="M3 1h3l1.5 4-2 1.2a9 9 0 0 0 4.3 4.3L11 8.5l4 1.5v3a2 2 0 0 1-2 2A12 12 0 0 1 1 3a2 2 0 0 1 2-2z"/></svg>02 8391 4627</li>
        <li><svg viewBox="0 0 16 16"><path d="M4 0h8a1 1 0 0 1 1 1v14a1 1 0 0 1-1 1H4a1 1 0 0 1-1-1V1a1 1 0 0 1 1-1zm1 2v10h6V2zm3 11a1 1 0 1 0 0 2 1 1 0 0 0 0-2z"/></svg>0417 552 908</li>
        <li><svg viewBox="0 0 16 16"><path d="M0 3h16v10H0zm1.5 1.5L8 9l6.5-4.5V4h-13z"/></svg>hello@halvora.au</li>
        <li><svg viewBox="0 0 16 16"><path d="M8 0a8 8 0 1 0 0 16A8 8 0 0 0 8 0zm0 1.5c1 0 2 2 2.3 5.5H5.7C6 3.5 7 1.5 8 1.5zM5.7 9h4.6C10 12.5 9 14.5 8 14.5S6 12.5 5.7 9zM1.6 7a6.5 6.5 0 0 1 3-4.8A13 13 0 0 0 4.2 7zm10.2 0a13 13 0 0 0-.4-4.8 6.5 6.5 0 0 1 3 4.8zM1.6 9h2.6a13 13 0 0 0 .4 4.8 6.5 6.5 0 0 1-3-4.8zm10.2 0h2.6a6.5 6.5 0 0 1-3 4.8 13 13 0 0 0 .4-4.8z"/></svg>www.halvora.au</li>
      </ul>
    </div>
  </section>
</main>
</body>
</html>
```